Storm Restoration Contractor needs a professional letterhead design

Looking for a professional letterhead design. Not looking for your cheapo MS Word standard ones that are readily available. Dont want it to be cookie cutter look like ones readily available online. We just recently changed our logo and want to freshen up all our documents. Our company handles restoring a property back to a pre-loss condition after a storm damages it. For example, wind, hail, flood, fire losses.

Target Market(s)

Property Owners, Homeowners, Property Owners, Commercial Property Owners, Property Management Companies

Industry/Entity Type

Construction Company

Requirements
Must have
• Professional, Use 1 of 2 logo options
• Storm Restoration, Roofing, Siding, Windows

```html
<!DOCTYPE html>
<html lang="en">
<head>
<meta charset="utf-8">
<title>Crestline Exteriors Letterhead</title>
<link href="https://fonts.googleapis.com/css2?family=Open+Sans:wght@400;600;700&display=swap" rel="stylesheet">
<style>
  :root {
    --brand-blue: #1f78bf;
    --brand-grey: #55575a;
    --text-dark: #333538;
    --paper: #ffffff;
    --backdrop: #e4e4e4;
  }
  * { box-sizing: border-box; margin: 0; padding: 0; }
  html, body {
    width: 1017px; height: 1200px; overflow: hidden;
    background: var(--backdrop);
    font-family: "Open Sans", Arial, sans-serif;
    color: var(--text-dark);
  }
  .letterhead {
    position: absolute; left: 105px; top: 30px;
    width: 806px; height: 1140px;
    background: var(--paper);
    box-shadow: 0 4px 18px rgba(0,0,0,0.15);
    overflow: hidden;
  }
  .brand {
    position: absolute; top: 70px; left: 0; right: 0;
    display: flex; flex-direction: column; align-items: center; gap: 12px;
  }
  .brand-dot {
    width: 78px; height: 78px; border-radius: 50%;
    background: var(--brand-blue);
  }
  .brand-name {
    font-size: 20px; font-weight: 700; letter-spacing: 2px;
    text-transform: uppercase; color: var(--brand-grey);
  }
  .recipient {
    position: absolute; top: 300px; left: 120px;
    font-size: 13px; line-height: 18px;
  }
  .recipient .recipient-name { font-weight: 700; }
  .letter-body {
    position: absolute; top: 410px; left: 140px; width: 530px;
    font-size: 13px; line-height: 18px;
  }
  .letter-body p { text-align: justify; margin-bottom: 20px; }
  .letter-body .closing { text-align: left; margin-top: 8px; }
  .signature {
    position: absolute; top: 890px; left: 175px;
    font-size: 13px; line-height: 18px;
  }
  .signature .signer { font-weight: 700; }
  .footer-bands {
    position: absolute; left: 0; bottom: 0; width: 806px; height: 70px;
  }
  .contact-line {
    position: absolute; left: 40px; bottom: 9px;
    display: flex; align-items: center; gap: 18px;
    font-size: 11.5px; color: #fff; white-space: nowrap;
  }
  .contact-line .address { font-weight: 700; }
  .contact-line .phone { display: flex; align-items: center; gap: 5px; }
  .contact-line svg { width: 11px; height: 11px; fill: #fff; }
</style>
</head>
<body>
  <main class="letterhead">
    <header class="brand">
      <div class="brand-dot"></div>
      <div class="brand-name">Crestline Exteriors</div>
    </header>

    <address class="recipient" style="font-style:normal">
      <div class="recipient-name">Mr. Daniel Reed</div>
      <div>Managing Director</div>
      <div>Northfield Holdings</div>
      <div>42 Elm Avenue</div>
      <div>USA</div>
    </address>

    <section class="letter-body">
      <p>Lorem ipsum dolor sit amet, consectetuer adipiscing elit. Nam cursus. Morbi ut mi. Nullam enim leo, egestas id, condimentum at, laoreet mattis, massa. Sed eleifend nonummy diam. Praesent mauris ante, elementum et, bibendum at, posuere sit amet, nibh. Duis tincidunt lectus quis dui viverra vestibulum.</p>
      <p>Suspendisse vulputate aliquam dui. Nulla elementum dui ut augue. Aliquam vehicula mi at mauris. Maecenas placerat, nisl at consequat rhoncus, sem nunc gravida justo, quis eleifend arcu velit quis lacus. Morbi magna magna, tincidunt a, mattis non, imperdiet vitae, tellus. Sed odio est, auctor ac, sollicitudin in, consequat vitae, orci. Fusce id felis. Vivamus sollicitudin.</p>
      <p>Metus eget eros. Pellentesque habitant morbi tristique senectus et netus et malesuada fames ac turpis egestas. In posuere felis nec tortor. Pellentesque faucibus. Ut accumsan ultricies elit. Maecenas at justo id velit placerat molestie. Donec dictum lectus non odio. Cras a ante vitae enim iaculis aliquam.</p>
      <p>Mauris nunc quam, venenatis nec, euismod sit amet, egestas placerat, est. Pellentesque habitant morbi tristique senectus et netus et malesuada fames ac turpis egestas. Cras id elit. Integer quis urna. Ut ante enim, dapibus malesuada, fringilla eu, condimentum quis, tellus. Aenean porttitor eros vel dolor. Donec convallis pede venenatis nibh. Duis quam. Nam eget.</p>
      <p class="closing">Thank you for being one of our valued customers.</p>
    </section>

    <div class="signature">
      <div class="signer">Name Here</div>
      <div>CEO</div>
    </div>

    <svg class="footer-bands" viewBox="0 0 806 70" preserveAspectRatio="none" aria-hidden="true">
      <polygon points="560,26 806,26 806,40 578,40" fill="var(--brand-grey)"/>
      <polygon points="0,40 574,40 556,70 0,70" fill="var(--brand-blue)"/>
    </svg>
    <div class="contact-line">
      <span class="address">215 Harbor Ridge Rd Ste 300, Millbrook, MD 20900</span>
      <span class="phone">
        <svg viewBox="0 0 24 24"><path d="M6.6 10.8a15.1 15.1 0 0 0 6.6 6.6l2.2-2.2a1 1 0 0 1 1-.25 11.4 11.4 0 0 0 3.6.57 1 1 0 0 1 1 1V20a1 1 0 0 1-1 1A17 17 0 0 1 3 4a1 1 0 0 1 1-1h3.5a1 1 0 0 1 1 1c0 1.25.2 2.45.57 3.57a1 1 0 0 1-.25 1z"/></svg>
        555-410-2200
      </span>
      <span class="phone">
        <svg viewBox="0 0 24 24"><path d="M6 3h12v5H6z M4 9h16a2 2 0 0 1 2 2v6h-4v4H6v-4H2v-6a2 2 0 0 1 2-2z M8 15v4h8v-4z"/></svg>
        555-410-2201
      </span>
    </div>
  </main>
</body>
</html>
```